Marlowe Group needs a business card

I would like the card to be simple but modern and elegant.
I like black and white.
or black and gold.
we are a private finance lender and also are involved in property and property developments.

please look at the business card photos i provided i would like M.G only one one side and all the other details on the other side use fonts that tie in with my theme.

Industry/Entity Type

Finance

Contact Information for Business Card

Marlowe Group (M.G) Daniel Marlowe M: 0413586207 E: danmarl@inboxmail.test

Font styles to use
Other font styles liked:
• Use fonts that would reflect our business

Colors
000000
ffffff

Requirements
Must have
• one side of details
• other side has either M.G or Marlowe Group like in the photos provided

```html
<!DOCTYPE html>
<html lang="en">
<head>
<meta charset="utf-8">
<title>Marlowe Group — Business Card</title>
<link rel="stylesheet" href="https://fonts.googleapis.com/css2?family=Source+Sans+3:wght@400;600&display=swap">
<style>
  :root {
    --backdrop: #6e4d36;
    --card-black: #000000;
    --card-white: #ffffff;
    --text-dark: #111111;
    --text-grey: #4a4a4a;
    --gold-deep: #a8893a;
    --gold-mid: #c9a94f;
    --gold-light: #f2dc83;
  }
  * { margin: 0; padding: 0; box-sizing: border-box; }
  html, body {
    width: 1200px;
    height: 987px;
    overflow: hidden;
  }
  body {
    position: relative;
    background: var(--backdrop);
    font-family: "Source Sans 3", "Myriad Pro", sans-serif;
  }
  .card {
    position: absolute;
    left: 293px;
    width: 615px;
    height: 352px;
  }
  .card--details {
    top: 130px;
    background: var(--card-white);
    border: 13px solid var(--card-black);
    display: flex;
    flex-direction: column;
    align-items: center;
    justify-content: center;
    text-align: center;
    padding-bottom: 14px;
  }
  .card__name {
    font-weight: 600;
    font-size: 26px;
    line-height: 32px;
    color: var(--text-dark);
    letter-spacing: 0.2px;
    margin-bottom: 6px;
  }
  .card__line {
    font-weight: 400;
    font-size: 18px;
    line-height: 26px;
    color: var(--text-grey);
  }
  .card--brand {
    top: 506px;
    padding: 14px;
    background: linear-gradient(180deg, var(--gold-light) 0%, var(--gold-mid) 18%, var(--gold-deep) 50%, var(--gold-mid) 82%, var(--gold-light) 100%);
  }
  .card__face {
    width: 100%;
    height: 100%;
    background: var(--card-black);
    display: flex;
    align-items: center;
    justify-content: center;
  }
  .card__brand-name {
    font-family: "Source Sans 3", "Myriad Pro", sans-serif;
    font-weight: 600;
    font-size: 58px;
    line-height: 1;
    color: var(--card-white);
    letter-spacing: 1px;
  }
</style>
</head>
<body>
  <section class="card card--details">
    <h1 class="card__name">Daniel Marlowe</h1>
    <p class="card__line">0413586207</p>
    <p class="card__line">danmarl@inboxmail.test</p>
    <p class="card__line">www.marlowegroup.test</p>
  </section>

  <section class="card card--brand">
    <div class="card__face">
      <span class="card__brand-name">Marlowe Group</span>
    </div>
  </section>
</body>
</html>
```